Medical Billing Company Needs a Business Card Design

We need a business card design for a Florida based medical billing company called 'Clinicians Keystone Solutions'. We specialize in providing revenue cycle management services to physician and therapist offices (we're basically their back-office processing partner for providing billing software, claims submissions, A/R follow-up and patient statements & collections. Our logo is red and blue-ish, so make sure that whatever other elements are used will match appropriately. Our current business card design has a too small font size. I'd like to project an image that shows we are modern & reliable. On a side note, I'm planning on using ZUB for printing these cards.

Target Market(s)

Office managers, physicians, therapists

Industry/Entity Type

Printing

Requirements
Must have
• Logo
Name of Employee
Phone
Fax
E-mail
Website

```html
<!DOCTYPE html>
<html lang="en">
<head>
<meta charset="utf-8">
<title>Clinicians Keystone Solutions – Business Card</title>
<link rel="stylesheet" href="https://fonts.googleapis.com/css2?family=Cabin:wght@400;500&display=swap">
<style>
  :root {
    --backdrop: #e4e4ea;
    --metal-dark: #3a3a3c;
    --metal-mid: #9a9a9c;
    --metal-light: #e2e2e2;
    --brand-blue: #2b2a7e;
    --brand-red: #b3202a;
    --ink-light: #eeeeee;
    --ink-grey: #6c6c6e;
    --rule: #c9c9cc;
  }
  * { margin: 0; padding: 0; box-sizing: border-box; }
  html, body {
    width: 1200px; height: 987px; overflow: hidden;
    background: var(--backdrop);
    font-family: "Cabin", "Gill Sans", sans-serif;
  }
  .canvas { position: relative; width: 1200px; height: 987px; }
  .card {
    position: absolute; left: 200px; width: 800px; height: 457px;
    border-radius: 36px; overflow: hidden;
    background: linear-gradient(100deg, var(--metal-dark) 0%, var(--metal-mid) 35%, var(--metal-light) 70%, #cfcfd1 100%);
    box-shadow: 0 6px 18px rgba(0,0,0,.18);
  }
  .card--back { top: 24px; }
  .card--front { top: 506px; }

  /* back */
  .back-mark {
    position: absolute; left: 0; right: 0; top: 140px;
    display: flex; align-items: center; justify-content: center; gap: 20px;
  }
  .back-mark__square {
    width: 44px; height: 44px; border: 3px solid var(--brand-blue); border-radius: 4px;
  }
  .back-mark__name {
    color: var(--brand-blue); font-size: 44px; font-weight: 500; letter-spacing: 3px;
  }
  .back-web {
    position: absolute; left: 0; right: 0; top: 300px; text-align: center;
    color: var(--ink-grey); font-size: 24px; letter-spacing: 2px;
  }

  /* front */
  .front-name {
    position: absolute; left: 60px; top: 50px;
    color: var(--brand-blue); font-size: 46px; font-weight: 400; letter-spacing: 2px;
  }
  .rule { position: absolute; right: 0; height: 3px; background: var(--rule); opacity: .8; }
  .rule--main { top: 250px; left: 0; }
  .rule--title { top: 310px; left: 560px; }
  .contact {
    position: absolute; left: 40px; top: 268px; list-style: none;
    color: var(--ink-light); font-size: 20px; line-height: 26px;
  }
  .contact li { display: flex; align-items: center; gap: 10px; }
  .contact svg { width: 14px; height: 14px; fill: none; stroke: var(--ink-light); stroke-width: 1.6; }
  .person { position: absolute; right: 60px; text-align: right; line-height: 1; }
  .person__name { top: 204px; color: var(--brand-blue); font-size: 36px; }
  .person__title { top: 266px; color: var(--brand-red); font-size: 28px; }
  .address {
    position: absolute; right: 60px; top: 332px; text-align: right;
    color: var(--ink-grey); font-size: 24px; line-height: 30px;
  }
</style>
</head>
<body>
<main class="canvas">
  <section class="card card--back" aria-label="Card back">
    <div class="back-mark">
      <span class="back-mark__square" aria-hidden="true"></span>
      <p class="back-mark__name">CLINICIANS KEYSTONE</p>
    </div>
    <p class="back-web">www.clinicianskeystone.com</p>
  </section>

  <section class="card card--front" aria-label="Card front">
    <h1 class="front-name">CLINICIANS KEYSTONE</h1>
    <p class="person person__name">Your Name</p>
    <div class="rule rule--main"></div>
    <p class="person person__title">Title</p>
    <div class="rule rule--title"></div>
    <ul class="contact">
      <li><svg viewBox="0 0 14 14"><circle cx="7" cy="7" r="5.5"/><path d="M5 4.5l1 2-1 1 1.5 1.5 1-1 2 1"/></svg>123-456-0789</li>
      <li><svg viewBox="0 0 14 14"><rect x="4" y="1.5" width="6" height="11" rx="1"/></svg>123-456-0789</li>
      <li><svg viewBox="0 0 14 14"><rect x="1.5" y="3" width="11" height="8"/><path d="M1.5 3l5.5 4.5 5.5-4.5"/></svg>info@clinicianskeystone.com</li>
      <li><svg viewBox="0 0 14 14"><circle cx="7" cy="7" r="5.5"/><path d="M1.5 7h11M7 1.5c-3 3-3 8 0 11M7 1.5c3 3 3 8 0 11"/></svg>www.clinicianskeystone.com</li>
    </ul>
    <p class="address">Street Name, City Name<br>State Zip Code</p>
  </section>
</main>
</body>
</html>
```